Web Site Design for a Finance (lending) Company

We are opening a new subsidiary that focuses on lending money in the real estate industry. We need a web site designed to represent the business.

The business is lending money to real estate investors. A typical client/borrower will be looking to borrow money to buy a house, renovate it and then sell it at a profit, all within 12 months or less.

Company name is RTV Finance. Our logo is attached.

Attached is a general outline for the web site. We're working on writing more text for each page but this should give you enough to get started with some ideas.

Competitor web site that I like a lot (as an example): https://dorvaleqcapital.example/. Many of the general items on this site match what we will need (description of loan programs, FAQ)

Target Market(s)

Real estate investors (generally individuals or small companies with just a few people) who are buying homes, renovating them and then selling them at a profit.

Industry/Entity Type

Finance

Coding

Coded - Design and coding required

Number of Pages Required

5+ page

Colors

Designer to choose colors to be used in the design.

Requirements
Must have
• Minimalist design. Clean lines without too much clutter. Some stock photography is ok but the photos should not be distracting. They should almost fade in to the background so that user can focus on the key information about what our company does instead. We are a finance company, not a design company, so the information about our products will be more interesting to site visitors than the art.
• Some minimalist examples from Snapboard:
• https://www.snapboardia.example/explore/minimalist-web-design/
Nice to have
• If you search in zoovle for "hard money lenders" you will find many examples of web sites from our competition. I have provided a link above to competitor web site that I like a lot.
• I have attached our logo in EPS format. Logo is green. Web site doesn't have to be green but it should be of a color that will work well with the logo.

```html
<!DOCTYPE html>
<html lang="en">
<head>
<meta charset="utf-8">
<title>RTV Finance – Real Estate Lending</title>
<link rel="stylesheet" href="https://fonts.googleapis.com/css2?family=Exo+2:wght@400;500&family=Roboto:wght@400;500;700&family=Open+Sans:ital,wght@0,400;0,600;1,400&display=swap">
<style>
:root{
  --green:#0b5230;
  --green-dark:#083d24;
  --green-bright:#1d7a3f;
  --gray:#8f9395;
  --gray-light:#efefef;
  --gray-text:#6b6b6b;
  --ink:#222;
  --white:#fff;
}
*{box-sizing:border-box;margin:0;padding:0}
html,body{width:1200px;height:3814px;overflow:hidden}
body{position:relative;background:var(--white);font-family:"Open Sans",Arial,sans-serif;color:var(--ink)}
.abs{position:absolute}
.h2{font-family:"Roboto",Arial,sans-serif;font-weight:400;font-size:40px;text-transform:uppercase;letter-spacing:.5px}
.h2 .soft{color:var(--gray)}
.btn{position:absolute;display:flex;align-items:center;justify-content:center;background:var(--gray);color:var(--white);font-family:"Roboto",Arial,sans-serif;font-weight:700;font-size:16px;text-transform:uppercase}
.lorem{font-size:14px;line-height:26px;color:var(--gray-text)}

/* header */
.brand{font-family:"Roboto",Arial,sans-serif;font-weight:700;color:var(--green);display:flex;align-items:center;gap:14px}
.brand .dot{width:18px;height:18px;background:var(--green)}
.topmail{left:684px;top:0;height:30px;display:flex;align-items:center;gap:8px;font-size:14px;color:var(--ink)}
.topphone{left:892px;top:0;width:228px;height:50px;background:var(--gray);color:var(--white);display:flex;align-items:center;justify-content:center;gap:10px;font-family:"Roboto",Arial,sans-serif;font-size:21px}
.nav{top:75px;left:577px;display:flex;gap:0;font-family:"Roboto",Arial,sans-serif;font-size:15px;text-transform:uppercase}
.nav a{color:var(--ink);text-decoration:none;padding:10px 16px;height:40px}
.nav a.active{background:var(--gray);color:var(--white)}

/* hero */
.hero{left:0;top:132px;width:1200px;height:547px;background:linear-gradient(100deg,#2e4a3a 0%,#5f7a70 45%,#3d5a4c 100%)}
.hero-person{left:60px;top:95px;width:290px;height:452px;background:linear-gradient(#2b3546,#1b2230);border-radius:120px 120px 0 0;opacity:.75}
.hero-title{right:80px;top:155px;text-align:right;font-family:"Exo 2",Arial,sans-serif;font-weight:500;color:var(--white);font-size:46px;line-height:56px;text-transform:uppercase}
.hero-text{right:80px;top:320px;width:700px;text-align:right;color:var(--white);font-size:15px;line-height:26px}
.hero .btn{right:80px;top:398px;width:206px;height:56px}
.dots{right:26px;top:195px;display:flex;flex-direction:column;gap:14px}
.dots span{width:17px;height:17px;border-radius:50%;background:var(--white)}
.dots span.on{background:transparent;border:3px solid var(--green-bright)}

/* features */
.feature{background:var(--white);text-align:center}
.feature .icon{width:126px;height:126px;border-radius:50%;background:var(--green);margin:0 auto;display:flex;align-items:center;justify-content:center;box-shadow:0 6px 10px rgba(0,0,0,.25)}
.feature h3{font-family:"Roboto",Arial,sans-serif;font-weight:500;font-size:17px;color:var(--green);text-transform:uppercase;margin-top:22px}
.feature p{font-size:13.5px;line-height:25px;color:var(--gray-text);margin:12px auto 0;width:270px}
.f-left{left:89px;top:612px;width:332px;height:308px;padding-top:34px}
.f-mid{left:427px;top:560px;width:346px;height:360px;padding-top:32px;border-left:1px solid #ddd;border-right:1px solid #ddd}
.f-right{left:773px;top:612px;width:338px;height:308px;padding-top:34px}

/* welcome */
.welcome{left:0;top:920px;width:1200px;height:440px;background:var(--gray-light)}
.welcome .h2{left:80px;top:82px;color:var(--green)}
.welcome .copy{left:80px;top:140px;width:640px}
.welcome .copy p{margin-bottom:14px}
.welcome .btn{left:80px;top:322px;width:186px;height:56px}
.money{left:818px;top:40px;width:250px;height:372px;background:linear-gradient(#9aa39a,#6f7d66 60%,#8a9080);border-radius:8px}

/* loan band */
.band{left:0;top:1360px;width:1200px;height:170px;background:var(--green);text-align:center;color:var(--white)}
.band .h2{position:static;margin-top:58px}
.band .sub{font-style:italic;font-size:14px;letter-spacing:.5px;margin-top:6px}
.notch{left:582px;top:1529px}
.loan-left{left:0;top:1530px;width:376px;height:572px;background:linear-gradient(#6f8f8a,#3f5a54)}
.loan-left .label{position:absolute;left:36px;top:222px;font-family:"Roboto",Arial,sans-serif;font-size:30px;color:var(--white);text-transform:uppercase}
.loan-card{left:376px;top:1530px;width:447px;height:572px;background:var(--white);text-align:center}
.loan-card h3{margin-top:148px;font-family:"Roboto",Arial,sans-serif;font-weight:400;font-size:30px;color:var(--green);text-transform:uppercase}
.loan-card p{width:380px;margin:14px auto 0;font-size:13.5px;line-height:28px;color:var(--gray-text)}
.loan-card .why{display:inline-block;margin-top:18px;font-style:italic;font-size:16px;color:var(--green);text-decoration:underline}
.loan-card .btn{left:126px;top:435px;width:186px;height:56px}
.loan-right{left:823px;top:1530px;width:377px;height:572px;background:linear-gradient(110deg,#c9c3b6,#8c8f95 60%,#5f6670)}

/* testimonials */
.testi{left:0;top:2102px;width:1200px;height:504px;background:linear-gradient(90deg,#2d2d2d,#4a4640 50%,#2f2f2f);text-align:center}
.testi .h2{position:static;margin-top:60px;color:var(--white)}
.testi .h2 .g{color:var(--green-bright)}
.quote-badge{width:60px;height:60px;border-radius:50%;background:var(--green);margin:22px auto 0;display:flex;align-items:center;justify-content:center}
.testi blockquote{width:830px;margin:24px auto 0;color:var(--white);font-size:14px;line-height:29px}
.testi .who{color:var(--green-bright);font-size:15px;margin-top:14px}
.avatars{left:0;top:360px;width:1200px;display:flex;justify-content:center;align-items:center;gap:20px}
.avatars span{width:86px;height:86px;border-radius:50%;border:3px solid var(--white);background:linear-gradient(#b9a894,#7c6c5c)}
.avatars .arrow{width:auto;height:auto;border:none;background:none;color:var(--white);font-size:34px;margin:0 14px}

/* blog */
.blog-title{left:0;top:2660px;width:1200px;text-align:center;color:var(--green)}
.post{top:2745px;width:252px;text-align:center}
.post .thumb{position:relative;height:190px}
.post .date{position:absolute;right:0;top:0;width:66px;height:88px;background:var(--green);color:var(--white);font-family:"Roboto",Arial,sans-serif;display:flex;flex-direction:column;align-items:center;justify-content:center;border:2px solid var(--white)}
.post .date b{font-size:32px;font-weight:500;line-height:36px}
.post .date i{font-size:12px;font-style:italic}
.post h4{margin-top:18px;font-family:"Roboto",Arial,sans-serif;font-weight:700;font-size:13.5px;line-height:24px;text-transform:uppercase}
.post a{display:inline-block;margin-top:12px;font-size:13px;font-weight:600;font-style:italic;color:var(--green);text-decoration:underline}

/* contact */
.contact{left:0;top:3084px;width:1200px;height:399px;background:var(--gray-light)}
.contact .h2{position:absolute;top:64px;left:0;width:1200px;text-align:center;color:var(--green)}
.contact .sub{position:absolute;top:118px;left:0;width:1200px;text-align:center;font-style:italic;font-size:17px;color:var(--ink)}
.field{position:absolute;background:var(--white);border:1px solid #d6d6d6;font-size:12px;color:var(--gray-text);padding:14px 12px}
.contact .btn{left:518px;top:286px;width:165px;height:56px}
.livechat{left:1152px;top:3196px;width:48px;height:194px;background:var(--gray);border-radius:8px 0 0 8px;color:var(--white);display:flex;flex-direction:column;align-items:center;justify-content:space-between;padding:14px 0}
.livechat span{writing-mode:vertical-rl;transform:rotate(180deg);font-family:"Roboto",Arial,sans-serif;font-size:15px;letter-spacing:1px}
.livechat .chat{width:48px;height:48px;background:var(--green);display:flex;align-items:center;justify-content:center;margin-bottom:-14px}

/* footer */
.footer{left:0;top:3483px;width:1200px;height:267px;background:var(--green);color:var(--white)}
.footer h5{font-family:"Roboto",Arial,sans-serif;font-weight:400;font-size:15px;text-transform:uppercase;margin-bottom:18px}
.col{position:absolute;top:42px;font-size:13px}
.sitemap li{list-style:none;line-height:33px;display:flex;align-items:center;gap:14px}
.sitemap li::before{content:"";width:7px;height:7px;background:#c9d6cf}
.crow{display:flex;gap:12px;align-items:flex-start;margin-bottom:14px}
.crow p{line-height:22px}
.social li{list-style:none;display:flex;align-items:center;gap:16px;margin-bottom:14px}
.social li span{width:44px;height:44px;border-radius:50%;border:2px solid #7fa591}
.copyright{left:0;top:3750px;width:1200px;height:64px;background:var(--gray);color:var(--white);display:flex;align-items:center;justify-content:center;font-size:14px}
.copyright b{color:var(--green);margin-right:4px}
</style>
</head>
<body>

<!-- header -->
<div class="abs brand" style="left:80px;top:30px;font-size:40px"><span class="dot"></span>RTV Finance</div>
<div class="abs topmail">
  <svg width="16" height="12" viewBox="0 0 16 12"><rect x="0.5" y="0.5" width="15" height="11" fill="none" stroke="#222"/><path d="M1 1l7 6 7-6" fill="none" stroke="#222"/></svg>
  info@RTVfinance.com
</div>
<div class="abs topphone">
  <svg width="18" height="18" viewBox="0 0 24 24"><path fill="#fff" d="M6.6 10.8c1.4 2.8 3.8 5.1 6.6 6.6l2.2-2.2c.3-.3.7-.4 1-.2 1.1.4 2.3.6 3.6.6.6 0 1 .4 1 1V20c0 .6-.4 1-1 1C10.6 21 3 13.4 3 4c0-.6.4-1 1-1h3.5c.6 0 1 .4 1 1 0 1.3.2 2.5.6 3.6.1.3 0 .7-.2 1L6.6 10.8z"/></svg>
  123 456 7890
</div>
<nav class="abs nav">
  <a class="active" href="#">Home</a><a href="#">About Us</a><a href="#">Loans</a><a href="#">Resources</a><a href="#">Contact Us</a>
</nav>

<!-- hero -->
<section class="abs hero" role="img" aria-label="Faded photo of a large suburban house with a smiling businessman holding a laptop">
  <div class="abs hero-person"></div>
  <h1 class="abs hero-title">Local Real Estate Experts<br>Lending to Local Real Estate<br>Investors</h1>
  <p class="abs hero-text">RTV Finance is a local business with local knowledge and strong industry relationships. A partner with a wide network who offers value added services.</p>
  <a class="btn" href="#">Contact Us</a>
  <div class="abs dots"><span></span><span></span><span class="on"></span><span></span><span></span></div>
</section>

<!-- features -->
<div class="abs feature f-left">
  <div class="icon"><svg width="64" height="64" viewBox="0 0 64 64" fill="none" stroke="#fff" stroke-width="5"><circle cx="30" cy="34" r="24"/><circle cx="30" cy="34" r="13"/><circle cx="30" cy="34" r="3" fill="#fff"/><path d="M30 34L54 10M46 8h10v10"/></svg></div>
  <h3>Mission</h3>
  <p>Lorem Ipsum is simply dummy text of the printing and typesetting industry.</p>
</div>
<div class="abs feature f-mid">
  <div class="icon"><svg width="66" height="66" viewBox="0 0 66 66" fill="none" stroke="#fff" stroke-width="4"><circle cx="33" cy="33" r="22"/><circle cx="33" cy="33" r="8"/><path d="M33 3v16M33 47v16M3 33h16M47 33h16"/></svg></div>
  <h3>Focus</h3>
  <p>Lorem Ipsum is simply dummy text of the printing and typesetting industry.</p>
  <svg style="margin-top:16px" width="36" height="18" viewBox="0 0 36 18"><path d="M0 9h32M24 2l8 7-8 7" fill="none" stroke="#0b5230" stroke-width="3"/></svg>
</div>
<div class="abs feature f-right">
  <div class="icon"><svg width="64" height="64" viewBox="0 0 64 64" fill="#fff"><text x="6" y="26" font-family="Roboto,Arial,sans-serif" font-size="24" font-weight="700">$</text><rect x="6" y="46" width="8" height="12"/><rect x="20" y="38" width="8" height="20"/><rect x="34" y="30" width="8" height="28"/><rect x="48" y="20" width="8" height="38"/><path d="M8 40L50 10" stroke="#fff" stroke-width="3"/><path d="M44 8h10v10z"/></svg></div>
  <h3>What Makes RTV Different</h3>
  <p>Lorem Ipsum is simply dummy text of the printing and typesetting industry.</p>
</div>

<!-- welcome -->
<section class="abs welcome">
  <h2 class="abs h2">Welcome to <span class="soft">RTV Finance</span></h2>
  <div class="abs copy lorem">
    <p>Lorem Ipsum is simply dummy text of the printing and typesetting industry. Lorem Ipsum has been the industry's standard dummy text ever since the 1500s, when an unknown printer took a galley of type and scrambled.</p>
    <p>Lorem Ipsum is simply dummy text of the printing and typesetting industry. Lorem Ipsum has been the industry's standard dummy text ever since the 1500s, when an unknown printer took a galley of type and scrambled it to make a type specimen book.</p>
  </div>
  <a class="btn" href="#">Know More</a>
  <div class="abs money" role="img" aria-label="Stack of banknotes with a small model house on top"></div>
</section>

<!-- loan program -->
<section class="abs band">
  <h2 class="h2">Our Loan <span class="soft">Program</span></h2>
  <p class="sub">WHAT WE OFFER</p>
</section>
<svg class="abs notch" width="36" height="16" viewBox="0 0 36 16" style="z-index:2"><path d="M0 0h36L18 16z" fill="#0b5230"/></svg>
<div class="abs loan-left" role="img" aria-label="Photo of a white two-storey house with a porch">
  <span class="label">Fix and Flip Loans</span>
</div>
<div class="abs loan-card">
  <h3>Fix and Flip Loans</h3>
  <p>Lorem Ipsum is simply dummy text of the printing and typesetting industry. Lorem Ipsum is simply</p>
  <p>Lorem Ipsum is simply dummy text of the printing and typesetting industry. Lorem Ipsum is simply dummy text of the printing and typesetting industry. Lorem Ipsum is simply dummy text of the printing.</p>
  <a class="why" href="#">Why Choose RTV</a>
  <a class="btn" href="#">Know More</a>
</div>
<div class="abs loan-right" role="img" aria-label="Photo of a hand holding house keys in front of a modern building"></div>

<!-- testimonials -->
<section class="abs testi" role="img" aria-label="Darkened photo of an agent with a couple in front of a for-sale sign">
  <h2 class="h2"><span class="g">What Our</span> Client Say</h2>
  <div class="quote-badge"><svg width="24" height="20" viewBox="0 0 24 20" fill="#fff"><path d="M0 20V10C0 4 3 1 9 0v4C6 5 5 7 5 10h5v10zM14 20V10c0-6 3-9 9-10v4c-3 1-4 3-4 6h5v10z"/></svg></div>
  <blockquote>" Lorem Ipsum is simply dummy text of the printing and typesetting industry. Lorem Ipsum has been the industry's standard dummy text ever since the 1500s, when an unknown printer took a galley of type and Lorem Ipsum is simply dummy text of the printing and typesetting industry. Lorem Ipsum has been the industry's standard "</blockquote>
  <p class="who">Client Name</p>
  <div class="abs avatars">
    <span class="arrow">‹</span><span></span><span></span><span></span><span class="arrow">›</span>
  </div>
</section>

<!-- blog -->
<h2 class="abs h2 blog-title">Latest <span class="soft">Blog</span></h2>
<article class="abs post" style="left:80px">
  <div class="thumb" role="img" aria-label="Photo of a couple signing papers with an agent" style="background:linear-gradient(#a7a094,#5f5a54)"><div class="date"><b>01</b><i>June</i></div></div>
  <h4>Lorem Ipsum is the simple<br>dummy text print</h4><a href="#">Read More.. »</a>
</article>
<article class="abs post" style="left:343px">
  <div class="thumb" role="img" aria-label="Photo of a businessman behind a row of small model houses" style="background:linear-gradient(#6d6560,#2f2b29)"><div class="date"><b>02</b><i>May</i></div></div>
  <h4>Lorem Ipsum is the simple<br>dummy text print</h4><a href="#">Read More.. »</a>
</article>
<article class="abs post" style="left:607px">
  <div class="thumb" role="img" aria-label="Photo of a handshake over a desk with a model house" style="background:linear-gradient(#b83a32,#6b2a26)"><div class="date"><b>01</b><i>April</i></div></div>
  <h4>Lorem Ipsum is the simple<br>dummy text print</h4><a href="#">Read More.. »</a>
</article>
<article class="abs post" style="left:872px">
  <div class="thumb" role="img" aria-label="Photo of a hand signing a contract next to a model house" style="background:linear-gradient(#e8e6e2,#a9a7a3)"><div class="date"><b>05</b><i>March</i></div></div>
  <h4>Lorem Ipsum is the simple<br>dummy text print</h4><a href="#">Read More.. »</a>
</article>

<!-- contact -->
<section class="abs contact">
  <h2 class="h2">Contact <span class="soft">Us</span></h2>
  <p class="sub">Need a free quote, or have a question? Get in touch!</p>
  <div class="field" style="left:140px;top:166px;width:302px;height:48px">First Name*</div>
  <div class="field" style="left:448px;top:166px;width:302px;height:48px">Email *</div>
  <div class="field" style="left:140px;top:221px;width:302px;height:48px">Last Name*</div>
  <div class="field" style="left:448px;top:221px;width:302px;height:48px">Phone*</div>
  <div class="field" style="left:758px;top:166px;width:302px;height:103px">How you heard about us *</div>
  <a class="btn" href="#">Submit</a>
</section>
<div class="abs livechat">
  <span>LIVE CHAT</span>
  <div class="chat"><svg width="20" height="18" viewBox="0 0 20 18" fill="#fff"><path d="M2 0h16a2 2 0 012 2v9a2 2 0 01-2 2H8l-5 5v-5H2a2 2 0 01-2-2V2a2 2 0 012-2z"/></svg></div>
</div>

<!-- footer -->
<footer class="abs footer">
  <div class="abs brand" style="left:80px;top:100px;font-size:32px;color:#fff"><span class="dot" style="background:#fff"></span>RTV Finance</div>
  <div class="col" style="left:343px">
    <h5>Sitemap</h5>
    <ul class="sitemap"><li>Home</li><li>About Us</li><li>Loans</li><li>Resources</li><li>Contact Us</li></ul>
  </div>
  <div class="col" style="left:608px;width:230px">
    <h5>Contact Us</h5>
    <div class="crow">
      <svg width="14" height="20" viewBox="0 0 14 20"><path fill="#fff" d="M7 0a7 7 0 017 7c0 5-7 13-7 13S0 12 0 7a7 7 0 017-7zm0 4a3 3 0 100 6 3 3 0 000-6z"/></svg>
      <p><b>RTV FINANCE</b><br>Lorem Ipsum is simply dummy text of the printing and types</p>
    </div>
    <div class="crow" style="align-items:center">
      <svg width="16" height="16" viewBox="0 0 24 24"><path fill="#fff" d="M6.6 10.8c1.4 2.8 3.8 5.1 6.6 6.6l2.2-2.2c.3-.3.7-.4 1-.2 1.1.4 2.3.6 3.6.6.6 0 1 .4 1 1V20c0 .6-.4 1-1 1C10.6 21 3 13.4 3 4c0-.6.4-1 1-1h3.5c.6 0 1 .4 1 1 0 1.3.2 2.5.6 3.6.1.3 0 .7-.2 1L6.6 10.8z"/></svg>
      <p style="font-size:15px"><b>123 456 7890</b></p>
    </div>
    <div class="crow" style="align-items:center">
      <svg width="16" height="12" viewBox="0 0 16 12"><rect width="16" height="12" fill="#fff"/><path d="M1 1l7 6 7-6" fill="none" stroke="#0b5230"/></svg>
      <p>info@RTVfinance.com</p>
    </div>
  </div>
  <div class="col" style="left:872px">
    <h5>Follow Us</h5>
    <ul class="social"><li><span></span>Friendbook</li><li><span></span>Chirper</li><li><span></span>Linkedly</li></ul>
  </div>
</footer>
<div class="abs copyright"><b>©RTV FINANCE</b> - 2017 All Right Reserved</div>

</body>
</html>
```